Business Cards for IT Consulting Company (Managed Service Provider)

I am looking to have some business cards printed and would like some designs. We are an IT Consulting company based in Vancouver BC. I would like a nice clean and modern look to the cards. I have uploaded all the versions of my logo so parts can be used as needed. Here is a snippit from our website homepage:

Quillbrook Networks Ltd. is an IT Solutions Partner located in Vancouver BC, Canada. We offer IT solutions and support to customers in the greater Vancouver Area. With expertise in Microsoft platforms, as well as Linux and Mac OSX and over 12 years experience in the IT industry, Quillbrook Networks is dedicated to offering our clients top quality service and products. We take pride in the solutions we offer our customers. The greatest compliment a client can give us is to recommend our services.

Quillbrook Networks Ltd. offers a wide range of IT services from onsite service to remote support and managed service solutions. This allows clients to choose the support path that best suits their company’s needs. Supporting many different sized companies from small to enterprise level over the past 12 years Quillbrook Networks has the experience and expertise needed to ensure things run smoothly. Allowing our clients to focus on doing business.

Revolutionizing the way IT services are delivered.

Quillbrook Networks is dedicated to providing our clients with IT solutions that work and grow with them for years to come. This philosophy helps save money in the long run instead of replacing equipment constantly. Far too often IT solutions are not well thought out and while possibly solving the problem at hand, require replacement due to growth or quality within a very short time frame. Quillbrook Networks takes pride in providing solutions that will last and be able to accommodate growth without the need for replacement.

Industry/Entity Type

Information Technology

Contact Information for Business Card

Quillbrook Networks Ltd.
(Employee Name)
Eml: (Employees Email Address)
Web: quillbrook.me
Ph: 604-555-0148

Font styles to use
Serif
Sans Serif

Requirements
Must have
• The Company logo and company colors.
Nice to have
• - Our tag line: "Revolutionizing IT Services" or "Revolutionizing the way IT services are delivered."
• - Also I really like the idea of nature and technology together blending which is sort of where my logo came from so integrating that somehow onto the business cards would be great.

```html
<!DOCTYPE html>
<html lang="en">
<head>
<meta charset="utf-8">
<title>Quillbrook Networks Ltd. — Business Card</title>
<link href="https://fonts.googleapis.com/css2?family=Montserrat:wght@400;500;600;700&display=swap" rel="stylesheet">
<style>
  :root {
    --canvas: #2b2b2b;
    --card: #000000;
    --ink: #ffffff;
    --accent: #1ea7e1;
    --card-w: 630px;
    --card-h: 360px;
  }
  * { box-sizing: border-box; margin: 0; padding: 0; }
  html, body {
    width: 1200px; height: 900px; overflow: hidden;
    background: var(--canvas);
    font-family: "Montserrat", sans-serif;
  }
  .canvas {
    position: relative; width: 1200px; height: 900px;
  }
  .card {
    position: absolute; left: 285px;
    width: var(--card-w); height: var(--card-h);
    background: var(--card); color: var(--ink);
    overflow: hidden;
    box-shadow: 0 14px 30px rgba(0,0,0,.45);
  }
  .card--front { top: 60px; }
  .card--back { top: 480px; }

  /* Front */
  .front-brand {
    position: absolute; left: 120px; top: 150px;
    display: flex; align-items: center; gap: 18px;
  }
  .brand-square {
    width: 44px; height: 44px; border: 3px solid var(--ink);
  }
  .front-brand .brand-name {
    font-size: 28px; font-weight: 600; letter-spacing: .5px;
  }
  .tagline {
    position: absolute; left: 200px; top: 205px;
    font-size: 16px; font-weight: 500; letter-spacing: 1px;
  }

  /* Back */
  .band-vertical {
    position: absolute; left: 100px; top: 0;
    width: 62px; height: 100%; background: var(--ink);
  }
  .band-horizontal {
    position: absolute; left: 0; top: 98px;
    width: 175px; height: 58px; background: var(--ink);
  }
  .band-mark {
    position: absolute; left: 110px; top: 106px;
    width: 42px; height: 42px; background: var(--accent);
  }
  .back-brand {
    position: absolute; left: 205px; top: 92px;
    font-size: 30px; font-weight: 700; color: var(--ink);
    letter-spacing: .3px; line-height: 1;
  }
  .contact {
    position: absolute; left: 205px; top: 160px;
  }
  .contact .person-name {
    font-size: 21px; font-weight: 700; color: var(--accent);
    letter-spacing: 1px; text-transform: uppercase;
  }
  .contact .person-role {
    font-size: 13px; font-weight: 500; letter-spacing: 1px;
    margin-top: 2px; text-transform: uppercase;
  }
  .contact-list {
    list-style: none; margin-top: 12px;
  }
  .contact-list li {
    display: flex; align-items: center; gap: 10px;
    font-size: 14px; font-weight: 500; letter-spacing: .4px;
    height: 24px;
  }
  .contact-list svg { width: 12px; height: 12px; flex: none; }
</style>
</head>
<body>
<main class="canvas">

  <section class="card card--front" aria-label="Card front">
    <div class="front-brand">
      <span class="brand-square" aria-hidden="true"></span>
      <span class="brand-name">Quillbrook Networks</span>
    </div>
    <p class="tagline" style="left:182px;top:208px;">Revolutionizing IT Services</p>
  </section>

  <section class="card card--back" aria-label="Card back">
    <div class="band-vertical"></div>
    <div class="band-horizontal"></div>
    <div class="band-mark" aria-hidden="true"></div>

    <p class="back-brand">Quillbrook Networks Ltd.</p>

    <div class="contact">
      <p class="person-name">Marla Trenholm</p>
      <p class="person-role">Director</p>
      <ul class="contact-list">
        <li>
          <svg viewBox="0 0 24 24" aria-hidden="true"><path fill="#1ea7e1" d="M6.6 10.8a15.1 15.1 0 0 0 6.6 6.6l2.2-2.2a1 1 0 0 1 1-.25 11.4 11.4 0 0 0 3.6.57 1 1 0 0 1 1 1V20a1 1 0 0 1-1 1A17 17 0 0 1 3 4a1 1 0 0 1 1-1h3.5a1 1 0 0 1 1 1c0 1.25.2 2.45.57 3.57a1 1 0 0 1-.25 1z"/></svg>
          604-555-0148
        </li>
        <li>
          <svg viewBox="0 0 24 24" aria-hidden="true"><rect x="3" y="5" width="18" height="14" fill="none" stroke="#1ea7e1" stroke-width="2"/><path d="M3 6l9 7 9-7" fill="none" stroke="#1ea7e1" stroke-width="2"/></svg>
          info@marlatrenholm.com
        </li>
        <li>
          <svg viewBox="0 0 24 24" aria-hidden="true"><circle cx="12" cy="12" r="9" fill="none" stroke="#1ea7e1" stroke-width="2"/><path d="M3 12h18M12 3c3 3.5 3 14.5 0 18M12 3c-3 3.5-3 14.5 0 18" fill="none" stroke="#1ea7e1" stroke-width="1.6"/></svg>
          www.quillbrook.me
        </li>
      </ul>
    </div>
  </section>

</main>
</body>
</html>
```